Single-sided business card for restaurant velmora with new logo made on this site

Business card options with new logo including restaurant name, address, phone number and website. This business card is single-sided only and will be presented at the hostess desk for clients to take. I would like to see options based on a cream card background, a white card background, a yellow card background and a burgundy colored background. It needs to be elegant and traditional.

Target Market(s)

local and international crowd

Industry/Entity Type

restaurant

Contact Information for Business Card

address, website and phone number

Font styles to use
Serif

Colors
EE7325
F08F49
F5BC92
FAE3D3
FDF4ED

Requirements
Must have
• new logo, address, phone number, website
Should not have
• more than three colors

```html
<!DOCTYPE html>
<html lang="en">
<head>
<meta charset="UTF-8">
<title>Restaurant Velmora – Business Card</title>
<link rel="stylesheet" href="https://fonts.googleapis.com/css2?family=Cinzel:wght@500;600&family=Montserrat:wght@400&display=swap">
<style>
  :root {
    --page-bg: #2b2b2b;
    --card-cream: #fdefd2;
    --card-glow: #fbe2b4;
    --accent-gold: #f0a830;
    --ink-brown: #3a1a12;
  }
  * { margin: 0; padding: 0; box-sizing: border-box; }
  html, body {
    width: 1200px;
    height: 800px;
    overflow: hidden;
    background: var(--page-bg);
  }
  .business-card {
    position: absolute;
    left: 35px;
    top: 80px;
    width: 1130px;
    height: 640px;
    background: var(--card-cream);
    overflow: hidden;
  }
  .card-backdrop {
    position: absolute;
    inset: 0;
    background: radial-gradient(ellipse 55% 60% at 55% 62%, var(--card-glow) 0%, rgba(251, 226, 180, 0.35) 55%, rgba(253, 239, 210, 0) 100%);
  }
  .brand-square {
    position: absolute;
    left: 498px;
    top: 121px;
    width: 133px;
    height: 133px;
    background: var(--accent-gold);
  }
  .brand-name {
    position: absolute;
    left: 0;
    right: 0;
    top: 278px;
    text-align: center;
    font-family: "Cinzel", serif;
    font-weight: 600;
    font-size: 46px;
    letter-spacing: 0.18em;
    color: var(--ink-brown);
  }
  .contact-block {
    position: absolute;
    left: 0;
    right: 0;
    top: 396px;
    text-align: center;
    color: var(--ink-brown);
  }
  .restaurant-title {
    font-family: "Cinzel", serif;
    font-weight: 600;
    font-size: 36px;
    letter-spacing: 0.01em;
    line-height: 1.2;
  }
  .contact-line {
    font-family: "Montserrat", sans-serif;
    font-weight: 400;
    font-size: 23px;
    letter-spacing: 0.02em;
    line-height: 1.2;
    margin-top: 16px;
  }
  .contact-line + .contact-line { margin-top: 19px; }
</style>
</head>
<body>
  <main class="business-card">
    <div class="card-backdrop" role="img" aria-label="Faint spiky plant leaves radiating from the lower centre in soft cream and pale gold tones"></div>
    <div class="brand-square"></div>
    <div class="brand-name">VELMORA</div>
    <section class="contact-block">
      <h1 class="restaurant-title">RESTAURANT VELMORA</h1>
      <p class="contact-line">Camelia 415, Bahía Serena, Oaxaca CP 70912</p>
      <p class="contact-line">P. 958-555-0142 w. velmora.com.mx</p>
    </section>
  </main>
</body>
</html>
```